Commercial Rooftop Solar business needs a website

We need a website with fantastic appeal for a new company based in Melbourne called Tallow Ridge Energy. We design and install solar energy systems for commercial applications across Australia. Our market is to focus on small to medium businesses looking for solar solutions, but we will also provide our service for residential customers. We would like a beautiful 'front page' feel to our home page, using photographs of solar PV systems and/or natural imagery. Our logo uses the colours orange and black, which could easily be echoed in photographic imagery of sunset and sunrise, for example. The design should communicate quiet confidence and professionalism to a corporate marketplace.

NEW POINTS FOR BRIEF: This design also needs to be flexible to allow for additional future content, including a Support page with sub pages, FAQ's, and a Blog.

As part of this design project, we will require the coding for the website to be completed by the designer.

We have seen some websites, which we like the look and feel of: these are listed below.

brightvanepower.com.au:

• Beautiful images underlaying brief text selling points.
• Simple ‘front cover’ style home page with elegant drop-down menu, stylish simple font style.
• Home page invites exploration through the menu links, rather than trying to provide all the information up front.
• Company logo and name in the top left hand corner, contact details accessible at top right hand, seems consistent in most sites.

kelpworks.com.au

rumbofield.com:
• Same element as the others is the front-page style home page with beautiful images underlying text.

We have a webpage that we started uploading content to. You can use some of the content there in your designs: www.tallowridgeenergy.com.au

Technical Specifications:
PAGES:

Home

About Us

Solutions - Commercial
- Residential

Products - Solar Panels - Vorla Heron, Vorla TELD, Vorla QB
- Solar Inverters - Kestamo, BrilQuill
- Monitoring systems - Dunmere Metrics
- Batteries - RW

- Datasheets have been provided for reference but if it's too much work, you can use generic text and we will provide content later.

Contact Us

FUTURE PAGES (Please consider in structure, where links could be placed):

Support

FAQ's

Blog.

We could provide some content for the Support page soon, but the Blog and FAQ's are future pages which we don't want highlighted in the design as we don't yet have content.

Phone: 1800 7 BIRCH
Email: sales@tallowridgeenergy.com.au

Currently, I do not have images and text available. Please
use placeholders in the meantime. The final text and images will be uploaded for the winner once a winning design has been selected.

Target Market(s)

Primary focus is on small to medium sized business owners. Those owners will have a house which may be suitable for solar so we want to cater to residential deeper in the website.

Industry/Entity Type

Solar Energy

Coding

Coded - Design and coding required

Number of Pages Required

5+ page

Colors
f78f20
0255a3

Requirements
Must have
• Logo as per attachments.
Nice to have
• Logo can have alternate colours Eg. White on Orange or Black etc. provided colour correct logo is shown somewhere eg. footer or contact page.
• In the active site, I'd like to have:
• Very slowly zooming images - barely perceptible.
• Title text that rolls into place
• Subtle movements
• See https://plumtally.com.au/ for example

```html
<!DOCTYPE html>
<html lang="en">
<head>
<meta charset="utf-8">
<title>Tallow Ridge Energy — Commercial Rooftop Solar</title>
<link href="https://fonts.googleapis.com/css2?family=Poppins:wght@300;400;500;600&family=Open+Sans:wght@300;400;600&display=swap" rel="stylesheet">
<style>
:root{
  --orange:#f4511e;
  --ink:#141414;
  --text:#3a3a3a;
  --line:#e6e6e6;
  --paper:#ffffff;
  --mist:#f3f3f3;
}
*{box-sizing:border-box;margin:0;padding:0}
html,body{width:1200px;height:3644px;overflow:hidden}
body{background:var(--paper);font-family:"Open Sans",Arial,sans-serif;color:var(--text);position:relative}

/* top bar */
.topbar{position:absolute;left:0;top:0;width:1200px;height:34px;background:var(--ink);color:#fff;font-size:12px;white-space:nowrap}
.topbar .mail{position:absolute;left:0;top:0;height:34px;width:330px;background:var(--orange);clip-path:polygon(0 0,100% 0,93% 100%,0 100%);display:flex;align-items:center;padding-left:40px;gap:8px}
.topbar .phone{position:absolute;left:352px;top:0;height:34px;display:flex;align-items:center;gap:8px}
.topbar .social{position:absolute;right:58px;top:11px;display:flex;gap:14px}
.dot{width:12px;height:12px;border-radius:50%;background:#fff;opacity:.85;display:inline-block}

/* header */
.header{position:absolute;left:0;top:34px;width:1200px;height:141px;background:var(--paper)}
.brand{position:absolute;left:61px;top:46px;display:flex;align-items:center;gap:16px}
.brand-mark{width:44px;height:44px;background:var(--orange);border-radius:50%}
.brand-name{font-family:"Poppins",sans-serif;font-weight:500;font-size:30px;color:var(--ink);letter-spacing:1px}
.contact-item{position:absolute;top:46px;display:flex;gap:20px;align-items:flex-start}
.contact-icon{width:40px;height:40px;border:2px solid var(--orange);border-radius:3px;display:flex;align-items:center;justify-content:center}
.contact-item .big{font-family:"Poppins",sans-serif;font-size:24px;color:var(--ink);line-height:28px}
.contact-item .small{font-size:14px;color:var(--ink)}

/* nav */
.nav{position:absolute;left:0;top:175px;width:1200px;height:51px;background:var(--ink)}
.nav a{position:absolute;top:15px;color:#fff;text-decoration:none;font-family:"Poppins",sans-serif;font-size:14px;font-weight:500}
.quote{position:absolute;right:0;top:0;width:267px;height:51px;background:var(--orange);clip-path:polygon(8% 0,100% 0,100% 100%,0 100%);color:#fff;font-family:"Poppins",sans-serif;font-size:18px;font-weight:500;display:flex;align-items:center;padding-left:52px}

/* hero */
.hero{position:absolute;left:0;top:226px;width:1200px;height:542px;color:#fff;text-align:center;overflow:hidden;
  background:
    radial-gradient(ellipse 220px 90px at 300px 440px,rgba(226,160,90,.55),transparent 70%),
    radial-gradient(ellipse 260px 110px at 900px 430px,rgba(226,160,90,.45),transparent 70%),
    radial-gradient(ellipse 520px 260px at 600px 230px,rgba(70,74,88,.9),transparent 75%),
    linear-gradient(180deg,#7c8796 0%,#4e5563 30%,#3a3c44 55%,#4a4038 80%,#2e2a27 100%)}
.hero::after{content:"";position:absolute;inset:0;background:rgba(0,0,0,.28)}
.hero .inner{position:absolute;inset:0;z-index:1}
.hero-brand{position:absolute;left:0;width:1200px;top:180px;font-family:"Poppins",sans-serif;font-weight:500;font-size:40px;letter-spacing:3px;color:#fff}
.hero h1{position:absolute;left:0;width:1200px;top:280px;font-family:"Poppins",sans-serif;font-weight:600;font-size:38px;letter-spacing:3px}
.hero p{position:absolute;left:315px;width:570px;top:344px;font-size:12px;line-height:22px;font-weight:300}
.btn{display:inline-block;background:var(--orange);color:#fff;font-family:"Poppins",sans-serif;font-size:15px;padding:0 26px;line-height:42px}
.hero .btn{position:absolute;left:553px;top:436px}

/* sections */
.section-title{position:absolute;left:0;width:1200px;text-align:center;font-family:"Poppins",sans-serif;font-weight:500;font-size:31px;color:var(--ink);letter-spacing:.5px}
.section-title span{color:var(--orange)}
.intro{position:absolute;left:240px;width:720px;top:862px;text-align:center;font-size:13px;line-height:25px;color:#555}
.ph{position:absolute}

/* features */
.card{position:absolute;width:345px;height:247px;border:1px solid var(--line);text-align:center;background:#fff}
.card .icon{width:70px;height:70px;margin:44px auto 0;border-radius:6px}
.card h3{font-family:"Poppins",sans-serif;font-weight:500;font-size:13px;color:var(--ink);margin-top:26px}
.card p{font-size:13px;color:#777;line-height:21px;margin:10px auto 0;width:260px}

/* projects */
.projects{position:absolute;left:0;top:1942px;width:1200px;height:707px;background:var(--mist)}
.caption{position:absolute;left:508px;top:2128px;width:232px;height:140px;background:rgba(20,20,20,.6);color:#fff;text-align:center;font-family:"Poppins",sans-serif}
.caption .t{font-size:23px;letter-spacing:1px;margin-top:44px}
.caption .s{font-size:12px;letter-spacing:1px;margin-top:4px}

/* blog */
.post{position:absolute;top:2778px;width:347px;height:405px;background:#fff;box-shadow:0 1px 6px rgba(0,0,0,.1)}
.post .img{height:230px}
.post h4{font-family:"Poppins",sans-serif;font-weight:500;font-size:14px;color:var(--ink);margin:24px 16px 0}
.post p{font-size:13px;line-height:20px;color:#666;margin:12px 16px 0}
.post .more{font-size:13px;color:#555;margin:16px 16px 0}

/* footer */
.footer{position:absolute;left:0;top:3234px;width:1200px;height:358px;background:linear-gradient(180deg,#3b3f42,#24282b);color:#fff;font-size:13px}
.footer h5{font-family:"Poppins",sans-serif;font-weight:500;font-size:15px}
.footer h5::after{content:"";display:block;width:28px;height:2px;background:#fff;margin-top:8px}
.fcol{position:absolute;top:50px}
.fcol li{list-style:none;line-height:34px;color:#ddd}
.field{width:212px;height:34px;background:#fff;color:#999;font-size:12px;padding-left:10px;line-height:34px;margin-top:12px}
.subscribe{display:inline-block;background:var(--orange);color:#fff;font-family:"Poppins",sans-serif;font-size:13px;font-weight:500;padding:0 16px;line-height:38px;margin-top:16px}
.finfo{display:flex;gap:16px;margin-bottom:22px}
.finfo .box{width:38px;height:38px;background:#fff;flex:none;display:flex;align-items:center;justify-content:center}
.finfo b{font-family:"Poppins",sans-serif;font-weight:500;font-size:12px;display:block}
.finfo span{font-size:12px;color:#ddd;line-height:17px}
.copy{position:absolute;left:0;top:3592px;width:1200px;height:52px;background:var(--orange);color:#fff;text-align:center;font-size:13px;line-height:52px}
</style>
</head>
<body>

<div class="topbar">
  <div class="mail">
    <svg width="14" height="10" viewBox="0 0 14 10"><rect x=".5" y=".5" width="13" height="9" fill="none" stroke="#fff"/><path d="M.5 .5 7 5.5 13.5 .5" fill="none" stroke="#fff"/></svg>
    Email: hello@tallowridgeenergy.com.au
  </div>
  <div class="phone">
    <svg width="12" height="12" viewBox="0 0 24 24"><path fill="#fff" d="M6.6 10.8a15 15 0 0 0 6.6 6.6l2.2-2.2c.3-.3.7-.4 1-.2 1.1.4 2.3.6 3.6.6.6 0 1 .4 1 1V20c0 .6-.4 1-1 1A17 17 0 0 1 3 4c0-.6.4-1 1-1h3.5c.6 0 1 .4 1 1 0 1.3.2 2.5.6 3.6.1.3 0 .7-.2 1z"/></svg>
    Phone: (+61) 3 9012 4478
  </div>
  <div class="social"><i class="dot"></i><i class="dot"></i><i class="dot"></i><i class="dot"></i><i class="dot"></i><i class="dot"></i></div>
</div>

<header class="header">
  <div class="brand"><span class="brand-mark"></span><span class="brand-name">Tallow Ridge Energy</span></div>
  <div class="contact-item" style="left:573px">
    <div class="contact-icon"><svg width="20" height="20" viewBox="0 0 24 24"><path d="M3 11 21 3l-8 18-2-8z" fill="none" stroke="#f4511e" stroke-width="2" stroke-linejoin="round"/></svg></div>
    <div><div class="big">1800 7 BIRCH</div><div class="small">sales@tallowridgeenergy.com.au</div></div>
  </div>
  <div class="contact-item" style="left:897px">
    <div class="contact-icon"><svg width="20" height="20" viewBox="0 0 24 24"><path d="M12 21s-7-7-7-12a7 7 0 0 1 14 0c0 5-7 12-7 12z" fill="none" stroke="#f4511e" stroke-width="2"/><circle cx="12" cy="9" r="2.5" fill="#f4511e"/></svg></div>
    <div><div class="big">48 Larkspur Rd,</div><div class="small">Richmond, Australia.</div></div>
  </div>
</header>

<nav class="nav">
  <a style="left:61px">Home</a>
  <a style="left:143px">About Us</a>
  <a style="left:253px">Solutions</a>
  <a style="left:365px">Products</a>
  <a style="left:471px">About</a>
  <a style="left:559px">Contact</a>
  <div class="quote">Get A Quote</div>
</nav>

<section class="hero" role="img" aria-label="Dusk photograph of a two-storey house with a pitched roof and lit windows">
  <div class="inner">
    <div class="hero-brand">TALLOW RIDGE ENERGY</div>
    <h1>WE WILL HELP YOU TO FIX YOUR ROOF</h1>
    <p>In a sunburnt country, harnessing the immense power of the sun for the energy requirements of your business is the most practical solution to sustain your business for the long term. This is energy that never runs out. Ask us how we can reduce your operating costs and protect your business.</p>
    <span class="btn">Read More</span>
  </div>
</section>

<h2 class="section-title" style="top:810px">WELCOME TO <span>ROOFERS</span></h2>
<p class="intro">Tallow Ridge Energy is a national company that specialises in solar solutions for the commercial market. We also provide solutions for the residential market, bringing our uncompromising quality and service to the home. The founder of the company has over 10 years experience delivering projects on both a residential and commercial scale, having overseen the installation of more than 3 megawatts of solar projects.</p>

<div class="ph" style="left:61px;top:1006px;width:347px;height:211px;background:linear-gradient(180deg,#9fb4c8,#2c4f86 55%,#c9a878)" role="img" aria-label="Ground-mounted solar panels on sandy terrain"></div>
<div class="ph" style="left:428px;top:1006px;width:347px;height:211px;background:linear-gradient(180deg,#dfe6e3,#c7cfc0 55%,#c9a21f)" role="img" aria-label="Wind turbines above a golden field"></div>
<div class="ph" style="left:792px;top:1006px;width:347px;height:211px;background:linear-gradient(180deg,#4f7fd0,#2c5bb0 60%,#a7b7d6)" role="img" aria-label="Technicians installing rooftop solar panels"></div>

<h2 class="section-title" style="top:1279px">WHY CHOOSE <span>TALLOW RIDGE</span></h2>

<div class="card" style="left:61px;top:1356px"><div class="icon" role="img" aria-label="Brick wall and trowel icon" style="background:linear-gradient(135deg,#e4574a,#b93d33)"></div><h3>ROOF REPAIRE</h3><p>Our services are so awesome of passages of Lerem ipsum available</p></div>
<div class="card" style="left:428px;top:1356px"><div class="icon" role="img" aria-label="Paint roller icon" style="background:linear-gradient(135deg,#8fd0e8,#e3a054)"></div><h3>SHINGLES</h3><p>Our services are so awesome of passages of Lerem ipsum available</p></div>
<div class="card" style="left:795px;top:1356px"><div class="icon" role="img" aria-label="Roof tiles icon" style="background:linear-gradient(135deg,#ee5b55,#c73e3a)"></div><h3>RE-ROOFING</h3><p>Our services are so awesome of passages of Lerem ipsum available</p></div>
<div class="card" style="left:61px;top:1628px"><div class="icon" role="img" aria-label="Worker with gear icon" style="background:linear-gradient(135deg,#3e7fd6,#f0a13a)"></div><h3>FAST AND EFFICIENT WORK</h3><p>Our services are so awesome of passages of Lerem ipsum available</p></div>
<div class="card" style="left:428px;top:1628px"><div class="icon" role="img" aria-label="House under umbrella icon" style="background:linear-gradient(135deg,#ef5b56,#f2a488)"></div><h3>PERSONALIZED SERVICE</h3><p>Our services are so awesome of passages of Lerem ipsum available</p></div>
<div class="card" style="left:795px;top:1628px"><div class="icon" role="img" aria-label="House with globe icon" style="background:linear-gradient(135deg,#c27b4a,#4caf50)"></div><h3>BEST PRICE GUARANTEE</h3><p>Our services are so awesome of passages of Lerem ipsum available</p></div>

<section class="projects"></section>
<h2 class="section-title" style="top:2003px">OUR LATEST <span>PROJECT</span></h2>
<div class="ph" style="left:61px;top:2085px;width:347px;height:228px;background:linear-gradient(180deg,#8ab8e6,#5a93d4 55%,#b8473a)" role="img" aria-label="Roofer working on a roof frame against blue sky"></div>
<div class="ph" style="left:428px;top:2085px;width:347px;height:228px;background:linear-gradient(180deg,#b46a3a,#d9a26a 50%,#6d6a52)" role="img" aria-label="Terracotta tiled house roof"></div>
<div class="caption"><div class="t">ROOFING IDEAS</div><div class="s">TALLOW RIDGE ENERGY</div></div>
<div class="ph" style="left:792px;top:2085px;width:347px;height:228px;background:linear-gradient(180deg,#c9c9c9,#8c8682 55%,#c8c23a)" role="img" aria-label="Roofer in safety vest laying shingles"></div>
<div class="ph" style="left:61px;top:2335px;width:347px;height:229px;background:linear-gradient(180deg,#9ec4ea,#6fa5da 55%,#3a5f8f)" role="img" aria-label="Engineers in hard hats reviewing a laptop beside solar panels"></div>
<div class="ph" style="left:428px;top:2335px;width:347px;height:229px;background:linear-gradient(180deg,#d9633f,#c24a2d 60%,#8f3422)" role="img" aria-label="Hands placing red roof tiles"></div>
<div class="ph" style="left:792px;top:2335px;width:347px;height:229px;background:linear-gradient(180deg,#4f8ad8,#2f5fa6 55%,#1f3c70)" role="img" aria-label="Technician installing solar panels"></div>

<h2 class="section-title" style="top:2705px">OUR <span>BLOG</span></h2>
<article class="post" style="left:66px"><div class="img" role="img" aria-label="Workers on a tiled roof with chimney" style="background:linear-gradient(180deg,#8fbde8,#b0653f 60%,#7a4a34)"></div><h4>Swedish Mega Project</h4><p>Contrary to popular belief, Lorem Ipsum is not simply random text. It has roots in a piece of classical Latin literature.</p><div class="more">Read more</div></article>
<article class="post" style="left:429px"><div class="img" role="img" aria-label="Roofer on a ladder at a house" style="background:linear-gradient(180deg,#9fc0e2,#6f6a68 55%,#a98f7a)"></div><h4>Pellentesque lacus varnus lorem</h4><p>Contrary to popular belief, Lorem Ipsum is not simply random text. It has roots in a piece of classical Latin literature.</p><div class="more">Read more</div></article>
<article class="post" style="left:791px"><div class="img" role="img" aria-label="Villa with terracotta roof" style="background:linear-gradient(180deg,#7fb0e0,#d0a26a 55%,#b5532c)"></div><h4>Cras ornare arcu avamus nda</h4><p>Contrary to popular belief, Lorem Ipsum is not simply random text. It has roots in a piece of classical Latin literature.</p><div class="more">Read more</div></article>

<footer class="footer" role="img" aria-label="Darkened landscape with wind turbines behind footer content">
  <div class="fcol" style="left:61px">
    <h5>News Letter</h5>
    <div style="font-size:12px;margin-top:16px">Sign up for our newsletter</div>
    <div class="field">Your Name*</div>
    <div class="field">Your Phone *</div>
    <span class="subscribe">SUBSCRIBE</span>
  </div>
  <div class="fcol" style="left:338px">
    <h5>Services</h5>
    <ul style="margin-top:8px"><li>Interior Renovation</li><li>Design and Build</li><li>Tiling and Painting</li><li>Paver Walkways</li><li>Household Repairs</li><li>Solar Systems</li></ul>
  </div>
  <div class="fcol" style="left:595px">
    <h5>Office Hours</h5>
    <ul style="margin-top:8px"><li>Monday : 0900 - 17:00</li><li>Tuesday : 0900 - 17:00</li><li>Wednesday : 0900 - 17:00</li><li>Thursday : 0900 - 17:00</li><li>Friday : 0900 - 17:00</li><li>Saturday, Sunday: By appointment only</li></ul>
  </div>
  <div class="fcol" style="left:892px;top:48px;width:250px">
    <div class="finfo"><div class="box"><svg width="16" height="16" viewBox="0 0 24 24"><path d="M3 11 12 3l9 8v10H3z" fill="#2b2f33"/></svg></div><div><b>ADDRESS:</b><span>48 Larkspur Rd Level 2<br>Richmond, VIC 3121</span></div></div>
    <div class="finfo"><div class="box"><svg width="12" height="16" viewBox="0 0 12 18"><rect x="1" y="1" width="10" height="16" rx="1.5" fill="none" stroke="#2b2f33" stroke-width="2"/></svg></div><div><b>PHONE:</b><span>03-9012-4478, 1800-724-274</span></div></div>
    <div class="finfo"><div class="box"><svg width="16" height="12" viewBox="0 0 16 12"><rect width="16" height="12" fill="#2b2f33"/><path d="M0 0 8 7 16 0" fill="none" stroke="#fff"/></svg></div><div><b>EMAIL:</b><span>support@tallowridgeenergy.com.au</span></div></div>
    <div style="border-top:1px solid rgba(255,255,255,.35);padding-top:18px;display:flex;align-items:center;gap:14px"><b style="font-family:Poppins,sans-serif;font-weight:500;font-size:15px">Social:</b><i class="dot"></i><i class="dot"></i><i class="dot"></i></div>
  </div>
</footer>
<div class="copy">© 2011-2017 Tallow Ridge Energy. All Right Reserved</div>

</body>
</html>
```